New website for a business that provides behaviour analysis

A new website that details the services that are provided around behaviour analysis for people with a disability through QPKV. There also needs to incorporate an about us and a staff page, Plus a referral form that is a google doc.
The business already has a web address that needs to be tailored.
Soft colours are preferred.
Do not have lots of pictures, keep them minimal.
A logo for the business is also needed to be incorporated, and this is a separate project that can be awarded to the website winner.
Website needs to be able to be used on WIX who will be the host for the design.

Target Market(s)

QPKV clients requiring behaviour support clician

Industry/Entity Type

Clinical behaviour support and analysis

Colors
00AB8E
00BBA5
67D7C9
C6EFE9
E9F9F6

Requirements
Must have
• Soft colours, preferable pale turquoise, minimal pictures, clean, sophisticated and classical look

```html
<!DOCTYPE html>
<html lang="en">
<head>
<meta charset="utf-8">
<title>CalmWave — About us</title>
<link href="https://fonts.googleapis.com/css2?family=Yeseva+One&family=Work+Sans:wght@400;500;600;700&display=swap" rel="stylesheet">
<style>
:root{
  --teal:#00AB8E;
  --teal-2:#00BBA5;
  --teal-3:#67D7C9;
  --mint:#C6EFE9;
  --mint-pale:#E9F9F6;
  --ink:#1f2b2a;
  --bg:#fcfefe;
  --navy:#1f2b6c;
  --pink:#e0245e;
}
*{box-sizing:border-box;margin:0;padding:0}
html,body{width:1200px;height:3416px;overflow:hidden}
body{font-family:"Work Sans",sans-serif;color:var(--ink);background:var(--bg);position:relative}
.serif{font-family:"Yeseva One",serif}
.wrap{position:absolute;left:164px;width:872px}
a{color:inherit;text-decoration:none}

/* top bar */
.topbar{position:absolute;top:0;left:0;width:1200px;height:70px;background:#fff}
.brand{position:absolute;left:164px;top:17px;font-family:"Yeseva One",serif;font-size:31px;color:var(--teal);letter-spacing:.5px}
.info{position:absolute;top:18px;display:flex;gap:9px;align-items:center}
.info svg{width:32px;height:32px}
.info .lbl{font-size:13px;color:var(--teal);font-weight:500;letter-spacing:.5px;line-height:18px}
.info .val{font-size:13.5px;color:var(--teal);line-height:18px}

/* nav */
.nav{position:absolute;top:70px;left:0;width:1200px;height:70px;background:var(--teal)}
.nav ul{position:absolute;left:164px;top:24px;display:flex;gap:19px;list-style:none;color:#fff;font-size:15.5px}
.nav li.active{font-weight:600}
.nav .search{position:absolute;left:837px;top:24px}
.btn-appt{position:absolute;left:884px;top:15px;width:152px;height:40px;border-radius:20px;background:var(--mint-pale);color:var(--teal);font-size:14.5px;font-weight:500;display:flex;align-items:center;justify-content:center}

/* hero */
.hero{position:absolute;top:140px;left:0;width:1200px;height:220px;background:linear-gradient(90deg,#b9c2c4,#d9d4cc 40%,#c9c1b6 70%,#bfc6c8)}
.hero .crumb{position:absolute;left:164px;top:70px;font-size:15px;color:var(--teal)}
.hero h1{position:absolute;left:164px;top:88px;font-size:44px;color:var(--teal);font-weight:400}
.hero .rule{position:absolute;left:268px;bottom:0;width:932px;height:7px;background:var(--teal)}

/* about */
.about-img{position:absolute;left:164px;top:416px;width:358px;height:447px;background:linear-gradient(160deg,#e9e6e2,#cfc9c3 60%,#f1efec)}
.about{position:absolute;left:541px;top:418px;width:495px}
.eyebrow{font-size:15px;font-weight:700;letter-spacing:3px;color:var(--teal);text-transform:uppercase}
.about h2{font-family:"Yeseva One",serif;font-weight:400;font-size:44px;line-height:48px;color:var(--teal);margin-top:10px}
.ticks{display:grid;grid-template-columns:222px 1fr;row-gap:14px;margin-top:20px;list-style:none;font-size:16px}
.ticks li{display:flex;align-items:center;gap:10px}
.ticks li::before{content:"";width:14px;height:14px;border-radius:50%;background:var(--teal)}
.about p{font-size:14px;line-height:19.5px;margin-top:22px}
.about p+p{margin-top:12px}

/* quote */
.quote{position:absolute;top:920px;left:0;width:1200px;height:387px;background:linear-gradient(90deg,#6fd4c4 0%,#45b9a6 45%,#1f8a78 100%);color:#fff;text-align:center}
.quote .mark{position:absolute;left:580px;top:56px}
.quote blockquote{position:absolute;left:310px;top:116px;width:580px;font-size:19px;line-height:27px}
.quote .line{position:absolute;left:503px;top:243px;width:194px;height:1px;background:rgba(255,255,255,.7)}
.quote cite{position:absolute;left:0;width:1200px;top:264px;font-style:normal;font-size:19px}
.quote .dots{position:absolute;left:567px;top:316px;display:flex;gap:9px}
.quote .dots span{width:16px;height:16px;border-radius:50%;background:#fff}

.sec-head{position:absolute;left:0;width:1200px;text-align:center}
.sec-head h2{font-family:"Yeseva One",serif;font-weight:400;font-size:30px;color:var(--teal);margin-top:4px}

/* doctors */
.doc{position:absolute;top:1477px;width:279px;height:472px}
.doc .photo{height:308px}
.doc .body{height:125px;background:var(--mint-pale);text-align:center;padding-top:22px}
.doc .name{font-size:15px;color:var(--teal)}
.doc .spec{font-size:15px;font-weight:700;letter-spacing:3px;color:var(--teal);margin-top:10px}
.social{display:flex;gap:18px;justify-content:center;margin-top:12px}
.social span{width:21px;height:21px;border-radius:50%;background:var(--teal)}
.doc .view{height:39px;background:var(--teal);color:#fff;font-size:14px;display:flex;align-items:center;justify-content:center}
.pager{position:absolute;left:567px;display:flex;gap:9px}
.pager span{width:16px;height:16px;border-radius:50%;background:var(--mint-pale)}
.pager span.on{background:var(--teal)}

/* news */
.news-bg{position:absolute;top:2050px;left:0;width:1200px;height:550px;background:#f6fbfb}
.article{position:absolute;width:427px;height:134px;background:#fff;display:flex}
.article .thumb{width:141px;height:134px;background:linear-gradient(135deg,#3a3f45,#8d8f94 55%,#d8d6d3)}
.article .txt{padding:18px 0 0 18px}
.article .meta{font-size:12px;color:var(--teal)}
.article h3{font-weight:400;font-size:16px;line-height:22px;margin-top:8px}
.article .stats{display:flex;gap:10px;align-items:center;font-size:12px;margin-top:14px}
.article .stats span{display:flex;gap:5px;align-items:center}

/* contact */
.cbox{position:absolute;top:2779px;width:205px;height:204px;background:var(--mint-pale);padding:45px 0 0 26px;color:var(--teal)}
.cbox.dark{background:var(--teal);color:#fff}
.cbox h4{font-size:15px;font-weight:700;margin-top:14px;letter-spacing:.3px}
.cbox p{font-size:14px;line-height:23px;margin-top:6px}
.cbox p small{font-size:12px}

/* footer */
.footer{position:absolute;top:3040px;left:0;width:1200px;height:376px;background:var(--teal);color:#fff}
.footer .logo{position:absolute;left:164px;top:66px;font-family:"Yeseva One",serif;font-size:31px}
.footer .tag{position:absolute;left:164px;top:118px;font-size:16px;line-height:22px}
.footer h5{position:absolute;top:62px;font-size:15px;font-weight:600}
.footer ul{position:absolute;top:116px;list-style:none;font-size:14px;line-height:26px}
.newsletter{position:absolute;left:795px;top:114px;width:240px;height:44px;background:var(--mint-pale);display:flex;align-items:center;justify-content:space-between;padding:0 14px 0 9px;color:var(--navy);font-size:14px}
.footer .hr{position:absolute;left:164px;top:252px;width:872px;height:1px;background:rgba(255,255,255,.6)}
.footer .copy{position:absolute;left:164px;top:300px;font-size:13.5px}
.footer .fsocial{position:absolute;left:937px;top:298px;display:flex;gap:18px}
.footer .fsocial span{width:21px;height:21px;border-radius:50%;background:#fff}
</style>
</head>
<body>

<header class="topbar">
  <div class="brand">CALMWAVE</div>
  <div class="info" style="left:490px">
    <svg viewBox="0 0 32 32" fill="none" stroke="#00AB8E" stroke-width="1.6"><path d="M8 5l5 5-3 3c1.5 3.5 4.5 6.5 8 8l3-3 5 5-3 4C14 26 5 17 4 8z"/><path d="M19 6a8 8 0 0 1 7 7M19 10a4 4 0 0 1 3 3"/></svg>
    <div><div class="lbl">EMERGENCY</div><div class="val">(555) 014-220-318</div></div>
  </div>
  <div class="info" style="left:667px">
    <svg viewBox="0 0 32 32" fill="none" stroke="#00AB8E" stroke-width="1.6"><circle cx="16" cy="16" r="12"/><path d="M16 9v7l-4 4"/></svg>
    <div><div class="lbl">WORK HOUR</div><div class="val">09:00 - 20:00 Everyday</div></div>
  </div>
  <div class="info" style="left:881px">
    <svg viewBox="0 0 32 32" fill="none" stroke="#00AB8E" stroke-width="1.6"><path d="M16 29s-10-9-10-16a10 10 0 0 1 20 0c0 7-10 16-10 16z"/><circle cx="16" cy="13" r="4"/></svg>
    <div><div class="lbl">LOCATION</div><div class="val">0123 Some Place</div></div>
  </div>
</header>

<nav class="nav">
  <ul><li>Home</li><li class="active">About us</li><li>Services</li><li>Doctors</li><li>News</li><li>Contact</li></ul>
  <svg class="search" width="22" height="22" viewBox="0 0 22 22" fill="none" stroke="#fff" stroke-width="1.8"><circle cx="9.5" cy="9.5" r="7.5"/><path d="M15 15l5 5"/></svg>
  <a class="btn-appt">Appointment</a>
</nav>

<section class="hero" role="img" aria-label="Photo of a smiling group of clinicians in white coats">
  <div class="crumb">Home / About</div>
  <h1>About us</h1>
  <div class="rule"></div>
</section>

<div class="about-img" role="img" aria-label="Photo of two smiling clinicians holding a tablet"></div>
<section class="about">
  <div class="eyebrow">Welcome to CalmWave</div>
  <h2>Best Care for Your Good Health</h2>
  <ul class="ticks">
    <li>A Passion for Healing</li><li>5-Star Care</li>
    <li>All our best</li><li>Believe in Us</li>
    <li>Always Caring</li><li>A Legacy of Excellence</li>
  </ul>
  <p>Lorem ipsum dolor sit amet, consectetur adipiscing elit. Quisque placerat scelerisque tortor ornare ornare. Quisque placerat scelerisque tortor ornare ornare Convallis felis vitae tortor augue. Velit nascetur proin massa in. Consequat faucibus porttitor enim et.</p>
  <p>Lorem ipsum dolor sit amet, consectetur adipiscing elit. Quisque placerat scelerisque. Convallis felis vitae tortor augue. Velit nascetur proin massa in.</p>
</section>

<section class="quote" role="img" aria-label="Teal-tinted photo of a clinician in a white coat with a stethoscope">
  <svg class="mark" width="40" height="28" viewBox="0 0 40 28" fill="#fff"><path d="M0 0h17v15l-7 13H3l5-12H0zM22 0h17v15l-7 13h-7l5-12h-8z"/></svg>
  <blockquote>Lorem ipsum dolor sit amet, consectetur adipiscing elit. Quisque placerat scelerisque tortor ornare ornare. Quisque placerat scelerisque felis vitae tortor augue. Velit nascetur Consequat faucibus porttitor enim et.</blockquote>
  <div class="line"></div>
  <cite>Sam Rivers</cite>
  <div class="dots"><span></span><span></span><span></span></div>
</section>

<div class="sec-head" style="top:1364px"><div class="eyebrow">Trusted Care</div><h2>Our Doctors</h2></div>

<article class="doc" style="left:164px">
  <div class="photo" role="img" aria-label="Photo of a smiling doctor with arms crossed" style="background:linear-gradient(160deg,#e7e9ee,#c9ccd3)"></div>
  <div class="body"><div class="name">Doctor’s Name</div><div class="spec">NEUROLOGY</div><div class="social"><span></span><span></span><span></span></div></div>
  <div class="view">View Profile</div>
</article>
<article class="doc" style="left:460px">
  <div class="photo" role="img" aria-label="Photo of a doctor in a tie with a stethoscope" style="background:linear-gradient(160deg,#eef0f1,#d2d6da)"></div>
  <div class="body"><div class="name">Doctor’s Name</div><div class="spec">NEUROLOGY</div><div class="social"><span></span><span></span><span></span></div></div>
  <div class="view">View Profile</div>
</article>
<article class="doc" style="left:757px">
  <div class="photo" role="img" aria-label="Photo of a doctor in a white coat in a clinic" style="background:linear-gradient(160deg,#cfe3b8,#eceae6 45%,#e4e2de)"></div>
  <div class="body"><div class="name">Doctor’s Name</div><div class="spec">NEUROLOGY</div><div class="social"><span></span><span></span><span></span></div></div>
  <div class="view">View Profile</div>
</article>
<div class="pager" style="top:1977px"><span></span><span class="on"></span><span></span></div>

<div class="news-bg"></div>
<div class="sec-head" style="top:2108px"><div class="eyebrow">Better information, Better health</div><h2>News</h2></div>

<article class="article" style="left:164px;top:2221px">
  <div class="thumb" role="img" aria-label="Photo of a doctor examining a patient"></div>
  <div class="txt"><div class="meta">Monday 05, September 2021 | By Author</div><h3>This Article’s Title goes Here,<br>but not too long.</h3>
  <div class="stats"><span><svg width="16" height="11" viewBox="0 0 16 11" fill="none" stroke="#3c5bd6" stroke-width="1.2"><path d="M1 5.5C3 2 5.5 1 8 1s5 1 7 4.5C13 9 10.5 10 8 10S3 9 1 5.5z"/><circle cx="8" cy="5.5" r="2"/></svg>68</span><span><svg width="13" height="12" viewBox="0 0 13 12" fill="none" stroke="#e0245e" stroke-width="1.3"><path d="M6.5 11S1 7.5 1 4a2.8 2.8 0 0 1 5.5-1A2.8 2.8 0 0 1 12 4c0 3.5-5.5 7-5.5 7z"/></svg>86</span></div></div>
</article>
<article class="article" style="left:609px;top:2221px">
  <div class="thumb" role="img" aria-label="Photo of a doctor examining a patient"></div>
  <div class="txt"><div class="meta">Monday 05, September 2021 | By Author</div><h3>This Article’s Title goes Here,<br>but not too long.</h3>
  <div class="stats"><span><svg width="16" height="11" viewBox="0 0 16 11" fill="none" stroke="#3c5bd6" stroke-width="1.2"><path d="M1 5.5C3 2 5.5 1 8 1s5 1 7 4.5C13 9 10.5 10 8 10S3 9 1 5.5z"/><circle cx="8" cy="5.5" r="2"/></svg>68</span><span><svg width="13" height="12" viewBox="0 0 13 12" fill="none" stroke="#e0245e" stroke-width="1.3"><path d="M6.5 11S1 7.5 1 4a2.8 2.8 0 0 1 5.5-1A2.8 2.8 0 0 1 12 4c0 3.5-5.5 7-5.5 7z"/></svg>86</span></div></div>
</article>
<article class="article" style="left:164px;top:2373px">
  <div class="thumb" role="img" aria-label="Photo of a doctor examining a patient"></div>
  <div class="txt"><div class="meta">Monday 05, September 2021 | By Author</div><h3>This Article’s Title goes Here,<br>but not too long.</h3>
  <div class="stats"><span><svg width="16" height="11" viewBox="0 0 16 11" fill="none" stroke="#3c5bd6" stroke-width="1.2"><path d="M1 5.5C3 2 5.5 1 8 1s5 1 7 4.5C13 9 10.5 10 8 10S3 9 1 5.5z"/><circle cx="8" cy="5.5" r="2"/></svg>68</span><span><svg width="13" height="12" viewBox="0 0 13 12" fill="none" stroke="#e0245e" stroke-width="1.3"><path d="M6.5 11S1 7.5 1 4a2.8 2.8 0 0 1 5.5-1A2.8 2.8 0 0 1 12 4c0 3.5-5.5 7-5.5 7z"/></svg>86</span></div></div>
</article>
<article class="article" style="left:609px;top:2373px">
  <div class="thumb" role="img" aria-label="Photo of a doctor examining a patient"></div>
  <div class="txt"><div class="meta">Monday 05, September 2021 | By Author</div><h3>This Article’s Title goes Here,<br>but not too long.</h3>
  <div class="stats"><span><svg width="16" height="11" viewBox="0 0 16 11" fill="none" stroke="#3c5bd6" stroke-width="1.2"><path d="M1 5.5C3 2 5.5 1 8 1s5 1 7 4.5C13 9 10.5 10 8 10S3 9 1 5.5z"/><circle cx="8" cy="5.5" r="2"/></svg>68</span><span><svg width="13" height="12" viewBox="0 0 13 12" fill="none" stroke="#e0245e" stroke-width="1.3"><path d="M6.5 11S1 7.5 1 4a2.8 2.8 0 0 1 5.5-1A2.8 2.8 0 0 1 12 4c0 3.5-5.5 7-5.5 7z"/></svg>86</span></div></div>
</article>
<div class="pager" style="top:2537px"><span></span><span class="on"></span><span></span></div>

<div class="sec-head" style="top:2667px"><div class="eyebrow">Get in touch</div><h2>Contact</h2></div>

<div class="cbox" style="left:164px">
  <svg width="32" height="32" viewBox="0 0 32 32" fill="none" stroke="currentColor" stroke-width="1.6"><path d="M8 5l5 5-3 3c1.5 3.5 4.5 6.5 8 8l3-3 5 5-3 4C14 26 5 17 4 8z"/><path d="M19 6a8 8 0 0 1 7 7M19 10a4 4 0 0 1 3 3"/></svg>
  <h4>EMERGENCY</h4><p>(555) 014-220-318<br>(555) 014-220-377</p>
</div>
<div class="cbox dark" style="left:386px">
  <svg width="32" height="32" viewBox="0 0 32 32" fill="none" stroke="currentColor" stroke-width="1.6"><path d="M16 29s-10-9-10-16a10 10 0 0 1 20 0c0 7-10 16-10 16z"/><circle cx="16" cy="13" r="4"/></svg>
  <h4>LOCATION</h4><p>0123 Some place<br>9876 Some country</p>
</div>
<div class="cbox" style="left:609px">
  <svg width="32" height="32" viewBox="0 0 32 32" fill="none" stroke="currentColor" stroke-width="1.6"><rect x="3" y="7" width="26" height="19"/><path d="M3 7l13 11 13-11"/></svg>
  <h4>EMAIL</h4><p>hello@calmwave.example<br><small>care@calmwave.example</small></p>
</div>
<div class="cbox" style="left:830px">
  <svg width="32" height="32" viewBox="0 0 32 32" fill="none" stroke="currentColor" stroke-width="1.6"><circle cx="16" cy="16" r="12"/><path d="M16 9v7l-4 4"/></svg>
  <h4>WORKING HOURS</h4><p>Mon-Sat 09:00-20:00<br>Sunday Emergency only</p>
</div>

<footer class="footer">
  <div class="logo">CALMWAVE</div>
  <div class="tag">Leading the Way in Medical<br>Execellence, Trusted Care.</div>
  <h5 style="left:406px">Important Links</h5>
  <ul style="left:406px"><li>Appointment</li><li>Doctors</li><li>Services</li><li>About Us</li></ul>
  <h5 style="left:560px">Contact Us</h5>
  <ul style="left:560px"><li>Call: (555) 014-220-318</li><li>Email: hello@calmwave.example</li><li>Address: 0123 Some place</li><li>Some country</li></ul>
  <h5 style="left:795px">Newsletter</h5>
  <div class="newsletter">Enter your email address
    <svg width="22" height="20" viewBox="0 0 22 20" fill="#1f2b6c"><path d="M21 1L1 9l7 3 2 7 3-5 5 3z"/></svg>
  </div>
  <div class="hr"></div>
  <div class="copy">© 2021 CalmWave All Rights Reserved by NORDLAY STUDIO</div>
  <div class="fsocial"><span></span><span></span><span></span></div>
</footer>

</body>
</html>
```